Letterhead for a German Distribution/Manufacturing Company

We need a professional Letterhead in a unique Design.
not to playful.
The Letterhead has to show show that we are a international company with headquater in Germany.
all details like adress, Vat Tax Number, Bank Accout, Eori, email, Company number has to be on the Letterhead.
for example use: VAT TAX DE5470318 Bank Account: Kestrel Bank IBAN DE412058731ß204683 Swift: MORV0417352 EORI 3150428697 Company Number: HRB 51806 Adress: VOLMINTA UG Ahornweg 7 Postal Code 06384 City Kellbrunn Country: Germany Email: info@volminta-example.com
the design can be colored but doesnt have to be
Industry/Entity Type
Manufacturing and international distribution
Requirements
Must have
- show that we are a international company with headquater in Germany. our company infos and logo

```html
<!DOCTYPE html>
<html lang="en">
<head>
<meta charset="utf-8">
<title>Volminta UG – Letterhead</title>
<link rel="stylesheet" href="https://fonts.googleapis.com/css2?family=Questrial&display=swap">
<style>
  :root {
    --backdrop: #ececec;
    --paper: #ffffff;
    --spine: #4b4b4b;
    --ink: #2f2f2f;
    --ink-soft: #555555;
  }
  * { margin: 0; padding: 0; box-sizing: border-box; }
  html, body {
    width: 1200px;
    height: 900px;
    overflow: hidden;
    background: var(--backdrop);
    font-family: "Questrial", "Century Gothic", sans-serif;
  }
  .canvas {
    position: relative;
    width: 1200px;
    height: 900px;
  }
  .letterhead {
    position: absolute;
    left: 303px;
    top: 30px;
    width: 594px;
    height: 840px;
    background: var(--paper);
    box-shadow: 0 2px 10px rgba(0, 0, 0, 0.08);
  }
  .letterhead__band {
    position: absolute;
    left: 0;
    top: 138px;
    width: 22px;
    bottom: 0;
    background: var(--spine);
  }
  .brand {
    position: absolute;
    top: 42px;
    right: 36px;
    display: flex;
    align-items: center;
    gap: 10px;
  }
  .brand__mark {
    width: 14px;
    height: 14px;
    border-radius: 50%;
    background: var(--ink);
  }
  .brand__name {
    font-size: 30px;
    letter-spacing: 1px;
    color: var(--ink);
    font-weight: 400;
  }
  .company-details {
    position: absolute;
    left: 42px;
    right: 24px;
    bottom: 34px;
    font-size: 14px;
    line-height: 1.6;
    color: var(--ink-soft);
    font-style: normal;
    white-space: nowrap;
  }
</style>
</head>
<body>
  <main class="canvas">
    <section class="letterhead">
      <div class="letterhead__band"></div>

      <header class="brand">
        <span class="brand__mark"></span>
        <span class="brand__name">VOLMINTA</span>
      </header>

      <address class="company-details">
        <div>E. info@volminta-example.com</div>
        <div>VOLMINTA UG Ahornweg 7 Postal Code 06384 City Kellbrunn, Germany</div>
        <div>VAT No. TAX DE5470318 | Company No. HRB 51806</div>
        <div>Bank A/c. Kestrel Bank IBAN DE412058731ß204683</div>
        <div>Swift A/c. MORV0417352 EORI 3150428697</div>
      </address>
    </section>
  </main>
</body>
</html>
```